Rollaway Stays

We are 100% online, promoting accommodation details and booking facilities for wheelchair dependant travellers.
Listings will only be accommodation providers which meet our specific criteria.

Target Market(s)

Wheelchair dependant people and their companions

Industry/Entity Type

Accommodation

Contact Information for Business Card

Name, mobile phone number, email address, website address

```html
<!DOCTYPE html>
<html lang="en">
<head>
<meta charset="utf-8">
<title>Rollaway Stays – Business Card</title>
<link href="https://fonts.googleapis.com/css2?family=Open+Sans:wght@400;700&display=swap" rel="stylesheet">
<style>
  :root {
    --stage: #e6e8eb;
    --charcoal: #2e2d2f;
    --charcoal-light: #3b3a3c;
    --paper: #ffffff;
    --ink: #2b2b2b;
    --red: #e31b3a;
    --rule: #3a3a3a;
  }
  * { box-sizing: border-box; margin: 0; padding: 0; }
  html, body {
    width: 1200px; height: 1024px; overflow: hidden;
    background: var(--stage);
    font-family: "Open Sans", Arial, sans-serif;
  }
  .sheet {
    width: 1200px; height: 1024px;
    display: flex; flex-direction: column; align-items: center; justify-content: center;
    gap: 48px;
  }
  .card {
    position: relative;
    width: 770px; height: 440px;
    border-radius: 26px;
    overflow: hidden;
  }
  /* Back of card */
  .card--back {
    background: linear-gradient(135deg, var(--charcoal-light), var(--charcoal));
  }
  .card--back .brand {
    position: absolute; right: 80px; top: 170px;
    display: flex; align-items: center; gap: 14px;
  }
  .brand__dot {
    flex: none;
    width: 30px; height: 30px; border-radius: 50%;
    background: var(--red);
  }
  .brand__name {
    font-weight: 700; font-size: 40px; letter-spacing: -0.5px;
    white-space: nowrap;
  }
  .card--back .brand__name { color: var(--paper); }
  .card--back .web {
    position: absolute; left: 40px; bottom: 34px;
    color: var(--red); font-size: 17px;
  }
  /* Front of card */
  .card--front {
    background: linear-gradient(160deg, #f3f3f3, var(--paper) 55%, #f1f1f1);
  }
  .card--front .brand {
    position: absolute; left: 56px; top: 76px;
    display: flex; align-items: center; gap: 14px;
  }
  .card--front .brand__name { color: var(--ink); }
  .card--front .name {
    position: absolute; right: 70px; top: 238px;
    color: var(--ink); font-weight: 700; font-size: 24px;
  }
  .card--front .divider {
    position: absolute; left: 56px; right: 40px; top: 300px;
    height: 1px; background: var(--rule);
  }
  .card--front .divider__accent {
    position: absolute; right: 30px; top: -1px;
    width: 130px; height: 3px; background: var(--red);
  }
  .contacts {
    position: absolute; left: 56px; right: 40px; top: 330px;
    display: flex; justify-content: space-between;
    list-style: none; font-size: 16px; color: var(--ink);
  }
  .contacts li { display: flex; align-items: center; gap: 8px; white-space: nowrap; }
  .contacts svg { width: 12px; height: 12px; fill: var(--red); }
  .card--front .edge {
    position: absolute; left: 0; right: 0; bottom: 0; height: 22px;
    background: var(--charcoal);
  }
</style>
</head>
<body>
<main class="sheet">
  <section class="card card--back" aria-label="Card back">
    <div class="brand">
      <span class="brand__dot"></span>
      <span class="brand__name">Rollaway Stays</span>
    </div>
    <p class="web">www.rollawaystays.com.au</p>
  </section>

  <section class="card card--front" aria-label="Card front">
    <div class="brand">
      <span class="brand__dot"></span>
      <span class="brand__name">Rollaway Stays</span>
    </div>
    <p class="name">Maya Corwell</p>
    <div class="divider"><span class="divider__accent"></span></div>
    <ul class="contacts">
      <li>
        <svg viewBox="0 0 12 12" aria-hidden="true"><rect x="3" y="0" width="6" height="12" rx="1.5"/></svg>
        555-014-2290
      </li>
      <li>
        <svg viewBox="0 0 12 12" aria-hidden="true"><rect x="0" y="2" width="12" height="8" rx="1"/></svg>
        hello@rollawaystays.com.au
      </li>
      <li>
        <svg viewBox="0 0 12 12" aria-hidden="true"><circle cx="6" cy="6" r="6"/></svg>
        www.rollawaystays.com.au
      </li>
    </ul>
    <div class="edge"></div>
  </section>
</main>
</body>
</html>
```